PowerPoint template for a tech startup

We need a PowerPoint template with a title slide, text slide, section slide, and thank you slide.
Our application helps engineering teams to be more productive. We would love a design that is slick, sophisticated, and consistent with our brand. (see more at www.velmo.ai or attached files)
By the way (not a requirement), Velmo means lighthouse in Greek.
Also, here is the font we used (not required) - https://glyphvault.net/fonts/league-gothic

• https://glyphvault.net/fonts/league-gothic

```html
<!DOCTYPE html>
<html lang="en">
<head>
<meta charset="utf-8">
<title>Velmo – Master Slide Presentation</title>
<link href="https://fonts.googleapis.com/css2?family=League+Gothic&family=Montserrat:wght@500;600;700;800&family=Open+Sans:wght@400;600;700&display=swap" rel="stylesheet">
<style>
:root{
  --navy:#1c4b74;
  --navy-deep:#15466f;
  --band:#17598a;
  --orange:#ea5b14;
  --orange-soft:#f08a3e;
  --ink:#3d3d3d;
  --muted:#7a7a7a;
  --grey-num:#9a9a9a;
  --slide-bg:#ececec;
  --page-box:#1d3f5e;
  --white:#ffffff;
}
*{box-sizing:border-box;margin:0;padding:0}
html,body{width:1200px;height:2956px;overflow:hidden;background:var(--white)}
body{position:relative;font-family:"Open Sans",sans-serif;color:var(--ink)}

.board-header{position:absolute;left:0;top:0;width:1200px;height:855px;background:var(--band)}
.board-logo{position:absolute;left:0;top:40px;width:1200px;text-align:center;font-family:"League Gothic",sans-serif;font-size:118px;line-height:1;color:var(--white);letter-spacing:2px}
.hero{position:absolute;left:187px;top:270px;width:557px;height:313px;transform:scale(1.483);transform-origin:top left;box-shadow:0 6px 20px rgba(0,0,0,.35)}

.slide{position:absolute;width:557px;height:313px;overflow:hidden;background:linear-gradient(135deg,#f6f6f6 0%,#e4e4e4 100%);box-shadow:0 2px 6px rgba(0,0,0,.18)}
.col-l{left:34px}.col-r{left:608px}

.wordmark{font-family:"League Gothic",sans-serif;line-height:1;color:var(--navy);letter-spacing:1px}
.wordmark.corner{position:absolute;right:22px;top:18px;font-size:38px}
.slide-title{position:absolute;left:22px;top:24px;font-family:"Montserrat",sans-serif;font-weight:700;font-size:19px;color:var(--navy)}
.slide-title::after{content:"";display:block;width:34px;height:2px;background:var(--orange);margin-top:6px}

.footer{position:absolute;left:0;bottom:0;width:100%;height:22px;background:var(--orange)}
.footer .url{position:absolute;left:20px;top:4px;font-size:9px;letter-spacing:3px;color:var(--white);font-weight:600}
.footer .social{position:absolute;right:62px;top:4px}
.footer .page{position:absolute;right:0;top:0;width:54px;height:22px;background:var(--page-box);color:var(--white);font-size:8px;text-align:center;line-height:22px}

.social{display:flex;gap:4px}
.social span{width:14px;height:14px;border-radius:50%;background:var(--white);display:block}
.social.dark span{background:var(--navy)}
.url-line{font-size:12px;letter-spacing:5px;color:#333}

/* title slide */
.title-left{position:absolute;left:60px;top:36px;width:240px;text-align:center}
.title-left .wordmark{font-size:52px}
.title-main{font-family:"Montserrat",sans-serif;font-weight:800;font-size:30px;line-height:1;margin-top:20px;color:var(--navy)}
.title-main.accent{color:var(--orange);margin-top:2px}
.pill{display:inline-block;background:var(--orange);color:var(--white);font-family:"Montserrat",sans-serif;font-weight:600;font-size:12px;padding:3px 8px;border-radius:3px;margin-top:6px}
.title-left .social{justify-content:center;margin-top:26px}
.title-left .url-line{margin-top:14px}
.hero-art{position:absolute;left:344px;top:0;width:213px;height:270px;background:linear-gradient(180deg,var(--orange-soft),var(--orange));border-radius:0 0 20px 20px}

/* centred logo slides */
.centre-stack{position:absolute;left:0;width:100%;text-align:center}
.centre-stack .social{justify-content:center;margin-top:14px}
.centre-stack .url-line{margin-top:12px}
.net-side{position:absolute;top:0;width:150px;height:100%}

/* table of content */
.toc{position:absolute;left:22px;top:68px;width:520px;display:grid;grid-template-columns:1fr 1fr;column-gap:20px;row-gap:14px}
.toc-item{display:flex;gap:8px}
.toc-num{font-family:"Montserrat",sans-serif;font-weight:700;font-size:26px;color:var(--grey-num);line-height:1;width:34px}
.toc-head{font-size:9px;color:var(--orange);font-weight:600}
.toc-text{font-size:6.5px;line-height:1.35;color:var(--ink)}

/* intro */
.photo{position:absolute}
.intro-text{position:absolute;left:240px;top:62px;width:300px}
.intro-text h2{font-family:"Montserrat",sans-serif;font-weight:700;font-size:18px;color:var(--navy)}
.intro-text h3{font-size:9px;color:var(--orange);font-weight:600;margin-top:12px}
.intro-text p{font-size:6.6px;line-height:1.45;margin-top:3px;text-align:justify}

/* agenda */
.agenda{position:absolute;left:40px;top:72px;width:480px;display:flex;justify-content:space-between}
.agenda-item{width:130px;text-align:center}
.agenda-dot{width:62px;height:62px;border-radius:50%;background:var(--orange);margin:0 auto;border:3px solid #f6b08a}
.agenda-item h4{font-family:"Montserrat",sans-serif;font-weight:600;font-size:8.5px;color:var(--navy);margin-top:18px}
.agenda-item p{font-size:6.6px;line-height:1.4;margin-top:6px;text-align:justify;text-align-last:center}

/* section */
.section-bg{position:absolute;inset:0;background:linear-gradient(100deg,#0e1a3e 0%,#232a55 45%,#5a4e6a 75%,#3a3a3e 100%)}
.section-text{position:absolute;left:58px;top:36px}
.section-text .wordmark{color:var(--white);font-size:52px}
.section-text .title-main{color:var(--white);font-size:28px;margin-top:14px}
.section-url{position:absolute;left:20px;bottom:18px;font-size:10px;letter-spacing:4px;color:var(--white)}

/* opportunity */
.donut{position:absolute;left:22px;top:66px}
.points{position:absolute;left:256px;top:66px;width:280px}
.point{border-left:2px solid var(--orange);padding-left:10px;margin-bottom:10px}
.point h5{font-size:8.5px;color:var(--orange);font-weight:600}
.point p{font-size:6.4px;line-height:1.35}
.point.f2{opacity:.85}.point.f3{opacity:.65}.point.f4{opacity:.45}.point.f5{opacity:.3}

/* strategy */
.steps{position:absolute;left:22px;top:80px;width:515px;display:flex;justify-content:space-between}
.step{width:96px;text-align:center}
.step svg{display:block;margin:0 auto}
.step-num{font-family:"Montserrat",sans-serif;font-weight:700;font-size:18px;color:#d4d4d4;margin-top:8px}
.step-dot{width:14px;height:14px;border-radius:50%;margin:2px auto 0;background:var(--orange)}
.step-dot.alt{background:var(--navy)}
.step h4{font-family:"Montserrat",sans-serif;font-weight:600;font-size:10px;color:var(--navy);margin-top:18px}
.step p{font-size:6.4px;line-height:1.35;color:var(--muted)}
.dotline{position:absolute;left:22px;top:164px;width:515px;border-top:2px dotted var(--navy)}

/* bar chart */
.bars{position:absolute;left:18px;top:76px}
.legend-list{position:absolute;left:300px;top:84px;width:240px}
.legend-list .point{border-left:2px solid var(--orange);margin-bottom:14px}

/* table */
.data-table{position:absolute;left:24px;top:76px;width:510px;border-collapse:collapse;background:var(--white);font-size:7px}
.data-table th{height:26px;color:var(--white);font-family:"Montserrat",sans-serif;font-weight:600;font-size:8px;background:var(--orange);border-right:1px solid #f4a67c}
.data-table th.lead{background:var(--navy);text-align:left;padding-left:10px;width:140px}
.data-table td{height:30px;text-align:center;font-weight:700;border-bottom:1px solid #e2e2e2;border-right:1px solid #e2e2e2;color:#222}
.data-table td.lead{text-align:left;padding-left:10px}

/* thank you */
.thanks-bg{position:absolute;inset:0;background:radial-gradient(circle at 50% 40%,#1f5f93 0%,var(--navy-deep) 70%)}
.thanks{font-family:"League Gothic",sans-serif;font-size:38px;line-height:1;margin-top:26px;letter-spacing:1px}
.thanks .t1{color:var(--orange)}.thanks .t2{color:var(--white)}
</style>
</head>
<body>

<header class="board-header">
  <div class="board-logo">VELMO</div>

  <!-- hero: title slide, shown large -->
  <section class="slide hero">
    <div class="title-left">
      <div class="wordmark">VELMO</div>
      <div class="title-main">MASTER SLIDE</div>
      <div class="title-main accent">PRESENTATION</div>
      <div class="pill">Subtittle of Presentation Goes Here</div>
      <div class="social dark"><span></span><span></span><span></span><span></span></div>
      <div class="url-line">www.velmo.ai</div>
    </div>
    <div class="hero-art" role="img" aria-label="Large orange lighthouse brand illustration"></div>
  </section>
</header>

<!-- row 1 -->
<section class="slide col-l" style="top:931px">
  <div class="title-left">
    <div class="wordmark">VELMO</div>
    <div class="title-main">MASTER SLIDE</div>
    <div class="title-main accent">PRESENTATION</div>
    <div class="pill">Subtittle of Presentation Goes Here</div>
    <div class="social dark"><span></span><span></span><span></span><span></span></div>
    <div class="url-line">www.velmo.ai</div>
  </div>
  <div class="hero-art" role="img" aria-label="Large orange lighthouse brand illustration"></div>
</section>

<section class="slide col-r" style="top:931px;background:var(--white)">
  <div class="net-side" style="left:0;background:linear-gradient(90deg,#dfe8f1,rgba(255,255,255,0))" role="img" aria-label="Blue network line pattern"></div>
  <div class="net-side" style="right:0;background:linear-gradient(270deg,#dfe8f1,rgba(255,255,255,0))" role="img" aria-label="Blue network line pattern"></div>
  <div class="centre-stack" style="top:88px">
    <div class="wordmark" style="font-size:96px">VELMO</div>
    <div class="social dark"><span></span><span></span><span></span><span></span></div>
    <div class="url-line">www.velmo.ai</div>
  </div>
</section>

<!-- row 2 -->
<section class="slide col-l" style="top:1262px;background:var(--navy-deep)">
  <div class="centre-stack" style="top:90px">
    <div class="wordmark" style="font-size:96px;color:var(--white)">VELMO</div>
    <div class="social"><span></span><span></span><span></span><span></span></div>
    <div class="url-line" style="color:var(--white)">www.velmo.ai</div>
  </div>
</section>

<section class="slide col-r" style="top:1262px">
  <h2 class="slide-title">Table Of Content</h2>
  <div class="wordmark corner">VELMO</div>
  <div class="toc">
    <div class="toc-item"><div class="toc-num">01</div><div><div class="toc-head">Content Here</div><div class="toc-text">Sample text that shows how a short note reads in this slot.</div></div></div>
    <div class="toc-item"><div class="toc-num">04</div><div><div class="toc-head">Content Here</div><div class="toc-text">Sample text that shows how a short note reads in this slot.</div></div></div>
    <div class="toc-item"><div class="toc-num">02</div><div><div class="toc-head">Content Here</div><div class="toc-text">Sample text that shows how a short note reads in this slot.</div></div></div>
    <div class="toc-item"><div class="toc-num">05</div><div><div class="toc-head">Content Here</div><div class="toc-text">Sample text that shows how a short note reads in this slot.</div></div></div>
    <div class="toc-item"><div class="toc-num">03</div><div><div class="toc-head">Content Here</div><div class="toc-text">Sample text that shows how a short note reads in this slot.</div></div></div>
    <div class="toc-item"><div class="toc-num">06</div><div><div class="toc-head">Content Here</div><div class="toc-text">Sample text that shows how a short note reads in this slot.</div></div></div>
  </div>
  <div class="footer"><span class="url">www.velmo.ai</span><div class="social"><span></span><span></span><span></span><span></span></div><span class="page">Page - 01</span></div>
</section>

<!-- row 3 -->
<section class="slide col-l" style="top:1600px">
  <div class="photo" style="left:0;top:52px;width:222px;height:212px;background:linear-gradient(180deg,#7fa6d4 0%,#4a6f95 55%,#2c3f56 100%)" role="img" aria-label="City skyline photo with connected network lines"></div>
  <div class="intro-text">
    <h2>Introduction</h2>
    <h3>Where can I get some?</h3>
    <p>Our platform helps engineering teams plan, build and ship with less friction. This slide gives a short overview of the product, the people who use it and the problems it solves every day. Replace this text with your own story and keep each line short so it is easy to read from the back of the room. Add one clear idea per paragraph, support it with a simple fact, and close with the point you want your audience to remember after the meeting ends. Keep the tone calm and direct.</p>
  </div>
  <div class="footer"><span class="url">www.velmo.ai</span><div class="social"><span></span><span></span><span></span><span></span></div><span class="page">Page - 02</span></div>
</section>

<section class="slide col-r" style="top:1600px">
  <h2 class="slide-title">Our Agenda</h2>
  <div class="wordmark corner">VELMO</div>
  <div class="agenda">
    <div class="agenda-item"><div class="agenda-dot"></div><h4>FIRST AGENDA</h4><p>Short sample text that explains this agenda point in a few plain lines for the team.</p></div>
    <div class="agenda-item"><div class="agenda-dot"></div><h4>SECOND AGENDA</h4><p>Short sample text that explains this agenda point in a few plain lines for the team.</p></div>
    <div class="agenda-item"><div class="agenda-dot"></div><h4>THIRD AGENDA</h4><p>Short sample text that explains this agenda point in a few plain lines for the team.</p></div>
  </div>
  <div class="footer"><span class="url">www.velmo.ai</span><div class="social"><span></span><span></span><span></span><span></span></div><span class="page">Page - 03</span></div>
</section>

<!-- row 4 -->
<section class="slide col-l" style="top:1929px">
  <div class="section-bg" role="img" aria-label="Photo of a lighthouse on a rocky shore at dusk"></div>
  <div class="section-text">
    <div class="wordmark">VELMO</div>
    <div class="title-main">SECTION SLIDE</div>
    <div class="pill">Subtittle of Presentation Goes Here</div>
  </div>
  <div class="section-url">www.velmo.ai</div>
</section>

<section class="slide col-r" style="top:1929px">
  <h2 class="slide-title">The Opportunity</h2>
  <div class="wordmark corner">VELMO</div>
  <svg class="donut" width="200" height="200" viewBox="0 0 200 200">
    <g transform="rotate(-90 100 100)" fill="none" stroke-width="26">
      <circle cx="100" cy="100" r="75" stroke="#d9d9d9" stroke-dasharray="12 459" stroke-dashoffset="-1"/>
      <circle cx="100" cy="100" r="75" stroke="#a9a9a9" stroke-dasharray="31 440" stroke-dashoffset="-15"/>
      <circle cx="100" cy="100" r="75" stroke="#6e6e6e" stroke-dasharray="92 379" stroke-dashoffset="-48"/>
      <circle cx="100" cy="100" r="75" stroke="var(--navy)" stroke-dasharray="139 332" stroke-dashoffset="-142"/>
      <circle cx="100" cy="100" r="75" stroke="var(--orange)" stroke-dasharray="186 285" stroke-dashoffset="-283"/>
    </g>
    <g font-family="Montserrat,sans-serif" font-weight="700" text-anchor="middle">
      <text x="100" y="96" font-size="16" fill="var(--navy)">THE</text>
      <text x="100" y="116" font-size="16" fill="var(--navy)">STRUCTURE</text>
      <text x="120" y="38" font-size="9" fill="#333">3%</text>
      <text x="170" y="68" font-size="9" fill="#fff">7%</text>
      <text x="167" y="140" font-size="9" fill="#fff">20%</text>
      <text x="78" y="176" font-size="9" fill="#fff">30%</text>
      <text x="38" y="62" font-size="9" fill="#fff">40%</text>
    </g>
  </svg>
  <div class="points">
    <div class="point"><h5>Content Here</h5><p>Sample text for this point that fits on two short lines of the slide.</p></div>
    <div class="point f2"><h5>Content Here</h5><p>Sample text for this point that fits on two short lines of the slide.</p></div>
    <div class="point f3"><h5>Content Here</h5><p>Sample text for this point that fits on two short lines of the slide.</p></div>
    <div class="point f4"><h5>Content Here</h5><p>Sample text for this point that fits on two short lines of the slide.</p></div>
    <div class="point f5"><h5>Content Here</h5><p>Sample text for this point that fits on two short lines of the slide.</p></div>
  </div>
  <div class="footer"><span class="url">www.velmo.ai</span><div class="social"><span></span><span></span><span></span><span></span></div><span class="page">Page - 05</span></div>
</section>

<!-- row 5 -->
<section class="slide col-l" style="top:2257px">
  <h2 class="slide-title">The Strategy</h2>
  <div class="wordmark corner">VELMO</div>
  <div class="dotline"></div>
  <div class="steps">
    <div class="step">
      <svg width="40" height="50" viewBox="0 0 40 50" fill="none" stroke="#333" stroke-width="2"><path d="M6 3h28M6 47h28M9 3c0 14 22 16 22 22S9 33 9 47M31 3c0 14-22 16-22 22s22 8 22 22"/></svg>
      <div class="step-num">01</div><div class="step-dot"></div><h4>INTEGRITY</h4><p>Short sample text for this step</p>
    </div>
    <div class="step">
      <svg width="50" height="50" viewBox="0 0 50 50" fill="none" stroke="#333" stroke-width="2"><circle cx="23" cy="27" r="19"/><circle cx="23" cy="27" r="12"/><circle cx="23" cy="27" r="5"/><path d="M23 27L44 6M38 6h6v6"/></svg>
      <div class="step-num">02</div><div class="step-dot alt"></div><h4>GOALS</h4><p>Short sample text for this step</p>
    </div>
    <div class="step">
      <svg width="40" height="50" viewBox="0 0 40 50" fill="none" stroke="#333" stroke-width="2"><path d="M20 10a13 13 0 0 0-7 24v6h14v-6a13 13 0 0 0-7-24zM14 44h12M20 2v4M6 8l3 3M34 8l-3 3"/></svg>
      <div class="step-num">03</div><div class="step-dot"></div><h4>INNOVATION</h4><p>Short sample text for this step</p>
    </div>
    <div class="step">
      <svg width="50" height="50" viewBox="0 0 50 50" fill="none" stroke="#333" stroke-width="2"><path d="M13 5h24v14a12 12 0 0 1-24 0zM13 9H5c0 8 4 12 9 12M37 9h8c0 8-4 12-9 12M25 31v8M16 45h18v-6H16z"/><path d="M25 10l2 5h5l-4 3 2 5-5-3-5 3 2-5-4-3h5z"/></svg>
      <div class="step-num">04</div><div class="step-dot alt"></div><h4>QUALITY</h4><p>Short sample text for this step</p>
    </div>
    <div class="step">
      <svg width="46" height="50" viewBox="0 0 46 50" fill="none" stroke="#333" stroke-width="2"><path d="M8 4v44M8 6h30l-7 9 7 9H8"/></svg>
      <div class="step-num">05</div><div class="step-dot"></div><h4>EXCELLENCE</h4><p>Short sample text for this step</p>
    </div>
  </div>
  <div class="footer"><span class="url">www.velmo.ai</span><div class="social"><span></span><span></span><span></span><span></span></div><span class="page">Page - 06</span></div>
</section>

<section class="slide col-r" style="top:2257px">
  <h2 class="slide-title">Bar Graph Chart</h2>
  <div class="wordmark corner">VELMO</div>
  <svg class="bars" width="270" height="180" viewBox="0 0 270 180" font-family="Open Sans,sans-serif" font-size="6" fill="#555">
    <g stroke="#cfcfcf" stroke-width=".6">
      <line x1="28" y1="150" x2="265" y2="150"/><line x1="28" y1="10" x2="28" y2="150"/>
    </g>
    <text x="10" y="22">75</text><text x="10" y="50">60</text><text x="10" y="78">45</text><text x="10" y="106">30</text><text x="10" y="134">15</text>
    <g>
      <rect x="40" y="92" width="13" height="58" fill="var(--navy)"/><rect x="55" y="46" width="13" height="104" fill="var(--orange)"/><rect x="70" y="112" width="13" height="38" fill="#b3b3b3"/>
      <rect x="100" y="100" width="13" height="50" fill="var(--navy)"/><rect x="115" y="68" width="13" height="82" fill="var(--orange)"/><rect x="130" y="120" width="13" height="30" fill="#b3b3b3"/>
      <rect x="160" y="104" width="13" height="46" fill="var(--navy)"/><rect x="175" y="84" width="13" height="66" fill="var(--orange)"/><rect x="190" y="120" width="13" height="30" fill="#b3b3b3"/>
      <rect x="220" y="112" width="13" height="38" fill="var(--navy)"/><rect x="235" y="84" width="13" height="66" fill="var(--orange)"/><rect x="250" y="124" width="13" height="26" fill="#b3b3b3"/>
    </g>
    <text x="50" y="162" font-size="5">Category 1</text><text x="110" y="162" font-size="5">Category 2</text><text x="170" y="162" font-size="5">Category 3</text><text x="230" y="162" font-size="5">Category 4</text>
  </svg>
  <div class="legend-list">
    <div class="point"><h5>Content Here</h5><p>Sample text for this point that fits on three short lines.</p></div>
    <div class="point f2"><h5>Content Here</h5><p>Sample text for this point that fits on three short lines.</p></div>
    <div class="point f3"><h5>Content Here</h5><p>Sample text for this point that fits on three short lines.</p></div>
  </div>
  <div class="footer"><span class="url">www.velmo.ai</span><div class="social"><span></span><span></span><span></span><span></span></div><span class="page">Page - 07</span></div>
</section>

<!-- row 6 -->
<section class="slide col-l" style="top:2595px">
  <h2 class="slide-title">Table Graph Chart</h2>
  <div class="wordmark corner">VELMO</div>
  <table class="data-table">
    <thead><tr><th class="lead">HEADING GOES HERE</th><th>TITTLE 1</th><th>TITTLE 2</th><th>TITTLE 3</th><th>TITTLE 4</th></tr></thead>
    <tbody>
      <tr><td class="lead">Sample row label text</td><td>123</td><td>123</td><td>123</td><td>123</td></tr>
      <tr><td class="lead">Sample row label text</td><td>456</td><td>456</td><td>456</td><td>456</td></tr>
      <tr><td class="lead">Sample row label text</td><td>789</td><td>789</td><td>789</td><td>789</td></tr>
      <tr><td class="lead">Sample row label text</td><td>123</td><td>123</td><td>123</td><td>123</td></tr>
      <tr><td class="lead">Sample row label text</td><td>456</td><td>456</td><td>456</td><td>456</td></tr>
    </tbody>
  </table>
  <div class="footer"><span class="url">www.velmo.ai</span><div class="social"><span></span><span></span><span></span><span></span></div><span class="page">Page - 08</span></div>
</section>

<section class="slide col-r" style="top:2595px">
  <div class="thanks-bg" role="img" aria-label="Faint world map over a deep blue background"></div>
  <div class="centre-stack" style="top:48px">
    <div class="wordmark" style="font-size:96px;color:var(--white)">VELMO</div>
    <div class="thanks"><span class="t1">THANK</span> <span class="t2">YOU</span></div>
    <div class="social"><span></span><span></span><span></span><span></span></div>
    <div class="url-line" style="color:var(--white)">www.velmo.ai</div>
  </div>
</section>

</body>
</html>
```